Lantern of Reeds: Book Cover Design + 6-Pages

**** PLEASE READ entire design brief attached!!!!!

Design Brief
A full colour digitally printed LANDSCAPE 8" (h) x 11"(w) hard cover book

1. Design front cover

PLUS

2. Design 6-pages

What is the book all about?
The Lantern of Reeds is a book for a young Goddess (aged 9 to 14 years old) approaching their first bleeding cycle. It is her time to learn about the women’s menstrual cycle and discover how it is the most earthly cycle women have and how it connects us to our intuition and to the wisdom of the moon.

Attached:
1. Complete brief
2. Front cover concept and suggested font

Target Market(s)

Target Market – women buying the Lantern of Reeds for a young girl aged 9 - 14
• Mother, mid-wife, auntie, grandmother, feminist, god mother, friend, sisters, nieces, cousins
• Yuppie hippy
• Disposable income
• Educated
• Travel overseas
• Have all new technology gadgets – brellix Cast, Zumaphone, Zumatabs, Brellix Cast etc
• New aged, spiritual
• Grass roots, shop local, home grown
• Feminist
• Educated
• Disposable income
• Yoga, Pilates, eat organically
• Value family and togetherness
• Value authentic gift giving

Industry/Entity Type

Landscape

Requirements
Nice to have
• I am looking for a wow factor (stunning, bold, striking, beautiful coffee table book) in the design because this is going to be a high quality gift.
There is a Goddess, spiritual fantasy theme.
I have supplied the front cover image that you may consider using, however I am open to your interpretation and creativity so you do not have to use this image if you do not wish.
I would like the design of this book to be universal as the story is to be translated into a number of languages.
Should not have
• Even though the book is for a 9 to 13 year girl, I am not looking for illustrations/animation

```html
<!DOCTYPE html>
<html lang="la">
<head>
<meta charset="utf-8">
<title>Lantern of Reeds – Book Spreads</title>
<link href="https://fonts.googleapis.com/css2?family=Cinzel:wght@400;600&family=Italianno&family=Old+Standard+TT:wght@400&display=swap" rel="stylesheet">
<style>
  :root {
    --canvas: #ece7de;
    --parchment-light: #f3e3bf;
    --parchment-mid: #e2c48c;
    --parchment-dark: #b9864a;
    --mist-blue: #cfe6f5;
    --mist-light: #f4f1ee;
    --mist-rose: #e4cbbf;
    --ink: #1f1a14;
    --gold: #b8862a;
    --gold-deep: #8a5a12;
    --vine: #5f9a3a;
    --vine-light: #a6cf6b;
    --moon: #2f79c9;
    --moon-ring: #d9e6ef;
  }
  * { box-sizing: border-box; margin: 0; padding: 0; }
  html, body { width: 1134px; height: 1200px; overflow: hidden; }
  body { background: var(--canvas); position: relative; font-family: "Old Standard TT", serif; color: var(--ink); }

  .spread { position: absolute; left: 85px; width: 956px; display: flex; box-shadow: 0 4px 14px rgba(0,0,0,.25); }
  .spread--one { top: 34px; height: 354px; }
  .spread--two { top: 420px; height: 355px; }
  .spread--three { top: 808px; height: 360px; }

  .page { position: relative; width: 50%; height: 100%; text-align: center; font-size: 10.6px; line-height: 16.5px; }
  .page--parchment { background: radial-gradient(ellipse at 50% 45%, var(--parchment-light) 30%, var(--parchment-mid) 75%, var(--parchment-dark) 100%); }
  .page--mist { background: radial-gradient(ellipse at 50% 50%, var(--mist-light) 10%, var(--mist-blue) 55%, var(--mist-rose) 90%, var(--parchment-mid) 100%); }
  .page--left { box-shadow: inset -12px 0 18px -12px rgba(80,50,20,.45); }
  .page--right { box-shadow: inset 12px 0 18px -12px rgba(80,50,20,.45); }

  .moon-ornament { position: absolute; top: -8px; width: 54px; height: 38px; border-radius: 0 0 27px 27px;
    background: radial-gradient(circle at 50% 45%, var(--moon) 45%, var(--moon-ring) 50%, var(--gold) 70%, transparent 72%); }
  .page--left .moon-ornament { right: 6px; }
  .page--right .moon-ornament { left: -48px; }
  .spread--one .page--right .moon-ornament { left: 176px; }
  .spread--one .page--left .moon-ornament { right: auto; left: 176px; }

  .vine { position: absolute; width: 34px; border-radius: 16px 16px 4px 4px;
    background: linear-gradient(180deg, transparent 0%, var(--vine-light) 20%, var(--vine) 100%); opacity: .85; }
  .page--left .vine { left: 8px; }
  .page--right .vine { right: 8px; }
  .spread--one .vine { top: 30px; bottom: 0; }
  .spread--two .vine, .spread--three .vine { top: 80px; bottom: 0; }

  .unicorn-figure { position: absolute; left: 30px; top: 150px; width: 70px; height: 100px; border-radius: 40% 50% 10% 10%;
    background: radial-gradient(ellipse, rgba(255,255,255,.85), rgba(255,255,255,0) 70%); }

  .text-block { position: absolute; left: 0; right: 0; }
  .text-block p + p { margin-top: 16px; }

  .celebration-script { position: absolute; left: 28px; top: 40px; font-family: "Italianno", cursive; font-size: 27px; color: var(--ink);
    display: flex; align-items: flex-end; gap: 6px; }
  .celebration-script::after { content: ""; width: 250px; border-bottom: 1px solid var(--gold-deep); margin-bottom: 8px; }
  .ceremony-title { position: absolute; left: 30px; right: 0; top: 66px; font-family: "Cinzel", serif; font-size: 16px; line-height: 22px; color: var(--gold); letter-spacing: .5px; }
  .welcome-line { font-family: "Cinzel", serif; font-size: 15px; line-height: 20px; color: var(--gold-deep); margin-top: 8px; }
  .love-from { position: absolute; left: 14px; bottom: 20px; font-family: "Italianno", cursive; font-size: 24px; display: flex; align-items: flex-end; gap: 6px; }
  .love-from::after { content: ""; width: 300px; border-bottom: 1px solid var(--gold-deep); margin-bottom: 7px; }

  .story-caption { font-family: "Cinzel", serif; font-size: 10.6px; line-height: 15px; color: var(--gold); text-transform: uppercase; margin-top: 12px; }
  .spread--three .page { font-size: 10.2px; line-height: 15.5px; }
</style>
</head>
<body>

<section class="spread spread--one">
  <article class="page page--parchment page--left">
    <div class="moon-ornament" role="img" aria-label="Blue moon ornament"></div>
    <div class="vine" role="img" aria-label="Climbing green vine"></div>
    <div class="celebration-script">In Celebration of</div>
    <h1 class="ceremony-title">A Sacred Honoring Of The<br>Transformation From Girl To Womanhood</h1>
    <div class="text-block" style="top:118px">
      <p>Nam dea<br>Haec, quae mundanis curru sella per publicum fecerit, non potest facere.<br>Volo enim vos a Phoenix capere,<br>Ut te ad fines terrae,<br>Et loquere ad cor meum tibi mortalium rerum lingua imis linguam nescit.</p>
      <p>Sequeretur quod naturalis mea oscula ore mortali combustion,<br>Etsi autem hoc posse comprehendi;<br>Sunt enim a Domino sapiunt,<br>Ah,<br>Volo tibi in aeternum<br>Ita vocant in solis ortum</p>
    </div>
  </article>
  <article class="page page--parchment page--right">
    <div class="moon-ornament" role="img" aria-label="Blue moon ornament"></div>
    <div class="vine" role="img" aria-label="Climbing green vine"></div>
    <div class="text-block" style="top:30px">
      <p>Sum dea ...<br>ut mihi Diana amat salietis iuxta fluvium cogitationes cordis ejus hunt<br>Pallas agit in subiecto, in me ut momenta et claritas,</p>
      <p>et sapientia, revelabit<br>Isis libenter meam quaerere in orbe terrarum et restituet te in quae cum caritate<br>Ego sum tranquillitas et fovens sementem,<br>tam quod ad rem mea Madonna momento</p>
      <p>Hera sese<br>cum fatigatus desieris contemnere aculeo Deus furari "tonitru cum fulmine icta<br>Hestia resonat et cursum imbuit et focis ut paulatim coxit</p>
      <p class="welcome-line" style="margin-top:4px">We welcome you<br>into our circle of womanhood.</p>
    </div>
    <div class="love-from">Love from</div>
  </article>
</section>

<section class="spread spread--two">
  <article class="page page--mist page--left">
    <div class="moon-ornament" role="img" aria-label="Blue moon ornament"></div>
    <div class="vine" role="img" aria-label="Climbing vine with sunflower"></div>
    <div class="text-block" style="top:52px">
      <p>En, quæ prodigia, ex oris allata remotis! Oras adveniunt pavefacta per<br>æquora nostras! Non equidem priscæ sæclum rediisse videtur<br>Pyrrhæ, cum Proteus pecus altos visere montes Et sylvas, egit.</p>
      <p>Sed tempora vix leviora Adsunt, evulsi quando radicitus alti<br>In mare descendunt montes, fluctusque pererrant. Quid vero hoc monstri est<br>magis et mirabile visu? Splendentes video, ceu pulchro ex ære vel auro<br>Conflatos, rutilisque accinctos undique gemmis, Baccâ cærulea, et<br>flammas imitante pyropo. Ex oriente adsunt, ubi gazas optima tellus<br>Parturit omnigenas, quibus æva per omnia sumptu<br>Ingenti finxere sibi diademata reges? Vix hoc crediderim.<br>Non fallunt talia acutos</p>
      <p class="story-caption">Grand daughter is asking her wise grandmother questions<br>about the women's bleeding cycle. Grandmother begins telling<br>her how women connected their bleeding cycle to time<br>many, many years ago.</p>
    </div>
  </article>
  <article class="page page--mist page--right">
    <div class="moon-ornament" role="img" aria-label="Blue moon ornament"></div>
    <div class="vine" role="img" aria-label="Climbing vine with sunflower"></div>
    <div class="text-block" style="top:52px">
      <p>Mercatorum oculos: prius et quam littora Gangis Liquissent, avidis gratissima<br>præda fuissent. Ortos unde putemus? An illos Ves'vius atrox<br>Protulit, ignivomisve ejecit faucibus Ætna? Luce micant propria,<br>Phœbive, per aëra purum</p>
      <p>Nunc stimulantis equos, argentea tela retorquent?<br>Phœbi luce micant. Ventis et fluctibus altis<br>Appulsi, et rapidis subter currentibus undis,<br>Tandem non fallunt oculos. Capita alta videre est<br>Multa onerata nive et canis conspersa pruinis.<br>Cætera sunt glacies. Procul hinc, ubi Bruma</p>
      <p class="story-caption">Grandmother explains how women connected their bleeding<br>cycle to the moon by watching and counting the number of<br>days between the new moon cycles.</p>
    </div>
  </article>
</section>

<section class="spread spread--three">
  <article class="page page--mist page--left">
    <div class="moon-ornament" role="img" aria-label="Blue moon ornament"></div>
    <div class="vine" role="img" aria-label="Climbing vine with sunflowers"></div>
    <div class="unicorn-figure" role="img" aria-label="White unicorn in soft light"></div>
    <div class="text-block" style="top:52px">
      <p>In glaciem aggesta sublimes vertice tandem Æquavit montes, non crescere<br>nescia moles. Sic immensa diu stetit, æternumque stetisset<br>Congeries, hominum neque vi neque mobilis arte, Littora ni tandem<br>declivia deseruisset,Pondere victa suo. Dilabitur. Omnia circum</p>
      <p>Antra et saxa gemunt, subito concussa fragore, Dum ruit in pelagum, tanquam<br>studiosa natandi,Ingens tota strues. Sic Delos dicitur olim,<br>Insula, in Ægæo fluitasse erratica ponto.Sed non ex glacie Delos;<br>neque torpida Delum Bruma inter rupes genuit nudum sterilemque.</p>
      <p>Sed vestita herbis erat illa, ornataque nunquam Decidua lauro; et Delum<br>dilexit Apollo.At vos, errones horrendi, et caligine digni</p>
      <p class="story-caption">Grandmother explains how women learnt how<br>the creation of a baby is connected to time and how<br>it took nine lunar months to birth a baby.</p>
    </div>
  </article>
  <article class="page page--mist page--right">
    <div class="moon-ornament" role="img" aria-label="Blue moon ornament"></div>
    <div class="vine" role="img" aria-label="Climbing vine with sunflowers"></div>
    <div class="text-block" style="top:44px">
      <p>Plangiumus fortes. Perière fortes, Patrium propter perière littus Bis quatèr centum;<br>subitò sub alto Æquore mersi. Navis, innitens lateri, jacebat,Malus ad summas<br>trepidabat undas, Cùm levis, funes quatiens, ad imumDepulit aura.<br>Plangimus fortes. Nimis, heu, caducam Fortibus vitam voluêre parcæ,<br>Nec sinunt ultrà tibi nos recentesNectere laurus,</p>
      <p>Magne, qui nomen, licèt incanorum,Traditum ex multis atavis tulisti!<br>At tuos olim memorabit ævumOmne triumphos.<br>Non hyems illos furibunda mersit,Non mari in clauso scopuli latentes,<br>Fissa non rimis abies, nec atroxAbstulit ensis. Navitæ sed tum nimium jocosi<br>Voce fallebant hilari laborem,Et quiescebat, calamoque dextram im-pleverat heros.</p>
      <p>Vox, quibus cordi est grave opus piumque, Humidum ex alto spolium levate,<br>Et putrescentes sub aquis amicosReddite amicis! Hi quidem (sic dis placuit) fuêre:<br>Sed ratis, nondum putris, ire possit Rursus in bellum, Britonumque nomen<br>Tollere ad astra.</p>
      <p class="story-caption" style="margin-top:2px">Grandmother explains how now women understood there<br>was a past, present and future from making a baby and this<br>was an important evolutionary jump for humans.<br>Past actions = present = being prepared for the future</p>
    </div>
  </article>
</section>

</body>
</html>
```